Vellisant - Quality health delivered at your door

Vellisant offers home and Community Based Services for adults who wish to continue live independently in their communities. We increase accessibility to health care, reduce health care delivery gap, reduce mortality and morbidity, reduce health while promoting healthy living in the comfort of our patients communities or homes.

We provide on site services and deliver high quality healthcare at your door. Our experienced physicians coordinate care with our certified nurse practitioners and provide chronic care management, physical therapy, rehabilitation and medications management.

Target Market(s)

Older population living in independent living facilities

Industry/Entity Type

Health Care

Contact Information for Business Card

Vellisant

Number of Pages Required

4 page

Font styles to use
Sans Serif

Colors

Designer to choose colors to be used in the design.

```html
<!DOCTYPE html>
<html lang="en">
<head>
<meta charset="utf-8">
<title>Vellisant - Quality health delivered at your door</title>
<link href="https://fonts.googleapis.com/css2?family=Marcellus&family=Lato:wght@400;700&display=swap" rel="stylesheet">
<style>
:root{
  --orange:#f6981a;
  --orange-deep:#e8890c;
  --green:#1f3405;
  --peach:#fbe8cc;
  --text:#555;
  --line:#c9c9c9;
  --white:#fff;
}
*{box-sizing:border-box;margin:0;padding:0}
html,body{width:1200px;height:2341px;overflow:hidden;background:var(--white)}
body{position:relative;font-family:'Lato',sans-serif;color:var(--text)}
.serif{font-family:'Marcellus',serif}
.abs{position:absolute}

/* header */
.site-header{position:absolute;left:0;top:0;width:1200px;height:136px;background:var(--white);border-top:5px solid var(--orange)}
.top-tab{position:absolute;left:421px;top:0;width:765px;height:44px;background:var(--orange);border-radius:0 0 40px 40px;display:flex;align-items:center;color:var(--white);font-size:16px}
.top-tab .item{display:flex;align-items:center;gap:10px;padding:0 26px;height:26px;border-right:1px solid rgba(31,52,5,.5)}
.top-tab .item:last-child{border-right:0;font-size:12px}
.top-tab .phone{padding-left:80px;font-size:18px}
.brand{position:absolute;left:74px;top:36px;display:flex;flex-direction:column;align-items:center;gap:8px}
.brand .dot{width:62px;height:62px;border-radius:50%;background:var(--orange)}
.brand .name{font-family:'Marcellus',serif;font-size:22px;color:var(--green);letter-spacing:.5px}
.main-nav{position:absolute;left:326px;top:80px;display:flex;gap:24px;font-family:'Marcellus',serif;font-size:15px;color:#444}
.main-nav .active{position:relative}
.main-nav .active::before{content:"";position:absolute;left:-2px;top:-10px;width:36px;height:36px;border:2px solid #fbdcb0;border-radius:50%}

/* hero */
.hero{position:absolute;left:0;top:136px;width:1200px;height:571px;background:linear-gradient(100deg,#cdb07c 0%,#e8c98e 30%,#d9b98a 50%,#b9bfc6 75%,#8f9aa6 100%)}
.hero-title{position:absolute;left:78px;top:290px;font-family:'Marcellus',serif;font-size:53px;color:var(--green)}
.hero-text{position:absolute;left:80px;top:368px;width:520px;font-size:20px;line-height:32px;color:#111}
.btn{position:absolute;display:flex;align-items:center;justify-content:center;font-family:'Marcellus',serif;font-size:21px;border-radius:3px}
.btn-dark{background:var(--green);color:var(--white)}
.btn-orange{background:var(--orange);color:var(--green);box-shadow:0 3px 0 var(--orange-deep)}
.arrow{position:absolute;width:50px;height:50px}

/* welcome */
.section-title{position:absolute;left:0;width:1200px;text-align:center;font-family:'Marcellus',serif;font-size:46px;color:var(--green)}
.section-title .accent{color:var(--orange)}
.welcome-copy{position:absolute;left:140px;top:826px;width:920px;text-align:center;font-size:16.5px;line-height:23px;color:#555}
.welcome-copy p+p{margin-top:22px}

/* services */
.services{position:absolute;left:0;top:1088px;width:1200px;height:587px;background:var(--peach)}
.services-sub{position:absolute;left:0;top:1208px;width:1200px;text-align:center;font-size:16px;line-height:22px}
.service-grid{position:absolute;left:78px;top:1303px;width:1046px;height:309px;display:grid;grid-template-columns:repeat(4,1fr);grid-template-rows:1fr 1fr}
.service{display:flex;flex-direction:column;align-items:center;justify-content:flex-start;padding-top:20px;font-family:'Marcellus',serif;font-size:18px;line-height:21px;color:#111;text-align:center;border-right:1px solid #6c7a2a;border-bottom:1px solid #6c7a2a}
.service:nth-child(4n){border-right:0}
.service:nth-child(n+5){border-bottom:0}
.service .icon{width:60px;height:60px;border-radius:10px;background:#6c6c6c;opacity:.55;margin-bottom:18px}
.service.highlight .icon{background:var(--green);opacity:1}
.service.highlight{color:var(--orange)}
.service.view-all{color:var(--orange);font-size:26px;padding-top:50px;gap:14px}

/* join */
.join-sub{position:absolute;left:0;top:1802px;width:1200px;text-align:center;font-size:14px}
.field{position:absolute;border-bottom:1px solid var(--line);font-size:13px;color:#888;padding:0 10px 10px}

/* footer */
.site-footer{position:absolute;left:0;top:2110px;width:1200px;height:231px;background:var(--orange);color:var(--white)}
.footer-nav{position:absolute;left:80px;top:42px;display:flex;gap:28px;font-family:'Marcellus',serif;font-size:14px}
.socials{position:absolute;left:956px;top:24px;display:flex;gap:14px}
.socials span{width:45px;height:45px;border-radius:50%;border:1.5px solid var(--green)}
.socials span:first-child{background:var(--green)}
.footer-rule{position:absolute;left:78px;top:101px;width:1046px;height:1px;background:var(--green)}
.contact{position:absolute;top:132px;display:flex;align-items:center;gap:16px;font-size:13.5px;line-height:20px}
.contact .badge{width:50px;height:50px;border-radius:50%;display:flex;align-items:center;justify-content:center;border:1.5px solid var(--green);flex:none}
.contact .badge.filled{background:var(--green)}
.copyright{position:absolute;right:80px;top:142px;text-align:right;font-size:13.5px;line-height:21px}
.copyright b{color:var(--green)}
</style>
</head>
<body>

<header class="site-header">
  <div class="top-tab">
    <div class="item phone">
      <svg width="12" height="18" viewBox="0 0 12 18"><rect x="1" y="1" width="10" height="16" rx="2" fill="none" stroke="#1f3405" stroke-width="2"/><circle cx="6" cy="14" r="1.2" fill="#1f3405"/></svg>
      123 456 7878
    </div>
    <div class="item">
      <svg width="20" height="14" viewBox="0 0 20 14"><rect width="20" height="14" rx="1" fill="#1f3405"/><path d="M1 1l9 7 9-7" fill="none" stroke="#f6981a" stroke-width="1.5"/></svg>
      info@vellisant.com
    </div>
    <div class="item">
      <svg width="14" height="14" viewBox="0 0 14 14"><circle cx="6" cy="6" r="4.5" fill="none" stroke="#1f3405" stroke-width="2"/><path d="M9.5 9.5L13 13" stroke="#1f3405" stroke-width="2"/></svg>
      Search...
    </div>
  </div>
  <div class="brand"><span class="dot"></span><span class="name">VELLISANT</span></div>
  <nav class="main-nav">
    <span class="active">Home</span><span>Assisted Living</span><span>Skilled Nursing</span><span>Independent Living</span><span>Services</span><span>Respite Care</span><span>Rehabilitation</span><span>Kindra</span>
  </nav>
</header>

<section class="hero" role="img" aria-label="Smiling senior couple embracing on a sunlit beach with tall grass"></section>
<h1 class="hero-title">VELLISANT</h1>
<p class="hero-text">Lorem Ipsum is simply dummy text of the printing and typesetting industry. Lorem Ipsum has been the</p>
<a class="btn btn-dark" style="left:78px;top:449px;width:165px;height:51px">LEARN MORE</a>
<a class="btn btn-orange" style="left:256px;top:449px;width:165px;height:49px">JOIN NOW</a>
<svg class="arrow" style="left:12px;top:387px" viewBox="0 0 50 50"><circle cx="25" cy="25" r="23" fill="none" stroke="#222" stroke-width="1.5"/><path d="M29 16l-9 9 9 9" fill="none" stroke="#222" stroke-width="2"/></svg>
<svg class="arrow" style="left:1136px;top:387px" viewBox="0 0 50 50"><circle cx="25" cy="25" r="23" fill="none" stroke="#222" stroke-width="1.5"/><path d="M21 16l9 9-9 9" fill="none" stroke="#222" stroke-width="2"/></svg>

<h2 class="section-title" style="top:752px"><span class="accent">Welcome To</span> VELLISANT</h2>
<div class="welcome-copy">
  <p>Vellisant offers home and Community Based Services for adults who wish to continue to live independently in the comfort of their communities.</p>
  <p>We provide on site services and deliver high quality healthcare at your door.&nbsp; Our experienced physicians coordinate care with our certified nurse practitioners and provide chronic care management, physical therapy, rehabilitation and medications management.</p>
</div>
<a class="btn btn-orange" style="left:517px;top:983px;width:165px;height:48px">READ MORE</a>

<section class="services"></section>
<h2 class="section-title" style="top:1135px"><span class="accent">Our</span> SERVICES</h2>
<p class="services-sub">Our mission is to provide the best service, care and match for<br>you and your family</p>
<div class="service-grid">
  <div class="service highlight"><span class="icon" role="img" aria-label="Stethoscope icon"></span>Comprehensive primary care<br>services</div>
  <div class="service"><span class="icon" role="img" aria-label="Nurse icon"></span>Coordination of speciality<br>care</div>
  <div class="service"><span class="icon" role="img" aria-label="Heart and stethoscope icon"></span>Asthma, Diabetes mellitus,<br>Heart</div>
  <div class="service"><span class="icon" role="img" aria-label="Brain scan icon"></span>Alzheimer's dementia</div>
  <div class="service"><span class="icon" role="img" aria-label="Caregiver with wheelchair icon"></span>Transitional Care</div>
  <div class="service"><span class="icon" role="img" aria-label="Nursing visit icon"></span>Skilled nursing visits for<br>wound care</div>
  <div class="service"><span class="icon" role="img" aria-label="Family and home icon"></span>Social services assessment</div>
  <div class="service view-all">View All Services
    <svg width="46" height="46" viewBox="0 0 46 46"><circle cx="23" cy="23" r="21" fill="none" stroke="#f6981a" stroke-width="2"/><path d="M20 15l8 8-8 8" fill="none" stroke="#f6981a" stroke-width="2"/></svg>
  </div>
</div>

<h2 class="section-title" style="top:1722px"><span class="accent">Join</span> US NOW</h2>
<p class="join-sub">If you have any questions about how we can help you please either send us an email or call us on below details...</p>
<div class="field" style="left:312px;top:1860px;width:283px">Name</div>
<div class="field" style="left:607px;top:1860px;width:284px">Email Id</div>
<div class="field" style="left:312px;top:1912px;width:579px;height:80px">Message...</div>
<a class="btn btn-dark" style="left:517px;top:2008px;width:165px;height:51px">SUBMIT</a>

<footer class="site-footer">
  <nav class="footer-nav"><span>Home</span><span style="margin-left:12px">Services</span><span>About</span><span>Assisted Living</span><span>Skilled Nursing</span><span>Independent Living</span><span>Contact</span></nav>
  <div class="socials" aria-label="Social links"><span></span><span></span><span></span></div>
  <div class="footer-rule"></div>
  <div class="contact" style="left:78px">
    <span class="badge filled"><svg width="18" height="24" viewBox="0 0 18 24"><path d="M9 1a8 8 0 0 0-8 8c0 6 8 14 8 14s8-8 8-14a8 8 0 0 0-8-8z" fill="#f6981a"/><circle cx="9" cy="9" r="3" fill="#1f3405"/></svg></span>
    <span>IOI - lorem Ipsum is the<br>simple Dummy Text.</span>
  </div>
  <div class="contact" style="left:343px">
    <span class="badge"><svg width="20" height="20" viewBox="0 0 24 24"><path d="M6.6 10.8a15 15 0 0 0 6.6 6.6l2.2-2.2a1 1 0 0 1 1-.25 11 11 0 0 0 3.6.6 1 1 0 0 1 1 1V20a1 1 0 0 1-1 1A17 17 0 0 1 3 4a1 1 0 0 1 1-1h3.5a1 1 0 0 1 1 1 11 11 0 0 0 .6 3.6 1 1 0 0 1-.25 1z" fill="#1f3405"/></svg></span>
    <span>123 456 7878</span>
  </div>
  <div class="contact" style="left:598px">
    <span class="badge"><svg width="20" height="14" viewBox="0 0 20 14"><rect width="20" height="14" rx="1" fill="#1f3405"/><path d="M1 1l9 7 9-7" fill="none" stroke="#f6981a" stroke-width="1.5"/></svg></span>
    <span>info@vellisant.com</span>
  </div>
  <div class="copyright">© <b>VELLISANT</b> 2017<br>All rights reserved.</div>
</footer>

</body>
</html>
```